New Business Card Design Project LORVANTI-Italy

we are LORVANTI-Italy
our company in the market for 3 years we are luxury cosmetic company and its about time for a facelift :)
i will like to have elegant luxurious and unique business card
that will give the person that get it a unique, luxurious and elegant impression
I'm VERY OPEN FOR NEW IDEAS , even duo i add a few files of things that i see on line and i like them

i add my logo as well
my website is LORVANTI.COM
(if you would like to see the main style that we have)

Target Market(s)

adult that have money :)

Industry/Entity Type

Business

Contact Information for Business Card

Name - Dario Lorvanti
Position - CEO and CO Founder
address - 4817 E Halvern
telephone - 555-384-1926
email - dario@lorvanti.com
fax - 555-384-1926
website - LORVANTI.COM

Colors
000000
959595
fbee3e
ffffff

Requirements
Must have
• big logo in GOLD color
• elegant look
• impressive
Nice to have
• not must but maybe classy pattern background
• not must but maybe emblem
• maybe clear plastic business card
Should not have
• colors
• images

```html
<!DOCTYPE html>
<html lang="en">
<head>
<meta charset="utf-8">
<title>LORVANTI-Italy Business Card</title>
<link rel="stylesheet" href="https://fonts.googleapis.com/css2?family=Cormorant+Garamond:wght@500;600&display=swap">
<style>
  :root {
    --stage: #1d1d1d;
    --card-black: #141414;
    --card-white: #ffffff;
    --gold: #c9a23a;
    --gold-edge: #a8832a;
    --grey: #6f6f6f;
  }
  * { margin: 0; padding: 0; box-sizing: border-box; }
  html, body { width: 1200px; height: 833px; overflow: hidden; }
  body {
    background: var(--stage);
    font-family: "Cormorant Garamond", Georgia, serif;
    position: relative;
  }
  .card {
    position: absolute;
    top: 268px;
    width: 520px;
    height: 297px;
    border-bottom: 4px solid var(--gold-edge);
    box-shadow: 0 14px 30px rgba(0,0,0,0.55);
  }
  .card-front { left: 50px; background: var(--card-black); }
  .card-back  { left: 630px; background: var(--card-white); }

  /* Front: brand mark area */
  .brand-front {
    position: absolute;
    left: 0; right: 0; top: 62px;
    display: flex; flex-direction: column; align-items: center; gap: 18px;
  }
  .brand-circle {
    width: 84px; height: 84px;
    border: 3px solid var(--gold);
    border-radius: 50%;
  }
  .brand-name {
    color: var(--gold);
    font-weight: 500;
    font-size: 46px;
    letter-spacing: 2px;
    line-height: 1;
  }

  /* Back: contact details */
  .contact {
    position: absolute;
    left: 34px; top: 40px;
    color: var(--grey);
    font-weight: 500;
    font-size: 16px;
    line-height: 1.2;
  }
  .contact-name { color: var(--gold); font-size: 23px; font-weight: 600; }
  .contact-role { margin-bottom: 10px; }
  .contact-company { color: var(--gold); font-weight: 600; font-size: 17px; }
  .contact-address { margin-bottom: 10px; }
  .contact-list { list-style: none; }
  .contact-list li { display: flex; align-items: center; gap: 8px; }
  .contact-list svg { width: 12px; height: 12px; flex: none; }

  .brand-back {
    position: absolute;
    right: 40px; top: 62px;
    display: flex; flex-direction: column; align-items: center; gap: 14px;
  }
  .brand-back .brand-circle { width: 130px; height: 130px; border-width: 4px; }
  .brand-back .brand-name { font-size: 26px; }
</style>
</head>
<body>
  <section class="card card-front" aria-label="Card front">
    <div class="brand-front">
      <div class="brand-circle"></div>
      <div class="brand-name">LORVANTI</div>
    </div>
  </section>

  <section class="card card-back" aria-label="Card back">
    <div class="contact">
      <div class="contact-name">Dario Lorvanti</div>
      <div class="contact-role">CEO and CO Founder</div>
      <div class="contact-company">LORVANTI-Italy</div>
      <div class="contact-address">4817 E Halvern</div>
      <ul class="contact-list">
        <li>
          <svg viewBox="0 0 12 12" aria-hidden="true"><path d="M2 1h3l1 3-2 1a7 7 0 0 0 3 3l1-2 3 1v3c-6 0-10-4-9-9z" fill="var(--gold)"/></svg>
          555-384-1926
        </li>
        <li>
          <svg viewBox="0 0 12 12" aria-hidden="true"><rect x="3" y="1" width="6" height="4" fill="var(--gold)"/><rect x="1" y="5" width="10" height="6" fill="var(--gold)"/></svg>
          555-384-1926
        </li>
        <li>
          <svg viewBox="0 0 12 12" aria-hidden="true"><rect x="1" y="2.5" width="10" height="7" fill="var(--gold)"/><path d="M1 2.5l5 4 5-4" stroke="#fff" stroke-width="1" fill="none"/></svg>
          dario@lorvanti.com
        </li>
        <li>
          <svg viewBox="0 0 12 12" aria-hidden="true"><circle cx="6" cy="6" r="5" stroke="var(--gold)" stroke-width="1.2" fill="none"/><path d="M1 6h10M6 1c-3 3-3 7 0 10M6 1c3 3 3 7 0 10" stroke="var(--gold)" stroke-width="1" fill="none"/></svg>
          LORVANTI.COM
        </li>
      </ul>
    </div>
    <div class="brand-back">
      <div class="brand-circle"></div>
      <div class="brand-name">LORVANTI</div>
    </div>
  </section>
</body>
</html>
```